Shine Fox Auto Care Business Card

2 side business card design for an auto detailing business

Target Market(s)

Auto detailing

Contact Information for Business Card

Things included

The business name “Shine Fox Auto Care”
Mark Dunrow
(403)271-6094
Kelmore Bay, Sk

Services offered - complete interior& exterior detail
- paint correction & protection
- ceramic coating
- trim restore
- auto carpet & seat cleaning

Requirements
Must have
• Colours that are in my logo

Services offered

My name Mark Dunrow
403-271-6094
Kelmore Bay, Sk

Not too sure in what order for these ?
Website. Shinefoxautocare.com
Instagram Shinefoxautocare
Email. Shinefoxautoac@mailvento.com

```html
<!DOCTYPE html>
<html lang="en">
<head>
<meta charset="utf-8">
<title>Shine Fox Auto Care — Business Card</title>
<link rel="stylesheet" href="https://fonts.googleapis.com/css2?family=Michroma&family=Montserrat:wght@400;500;700&display=swap">
<style>
  :root {
    --canvas: #8a8a8a;
    --ink: #1c1b1d;
    --paper: #ffffff;
    --brand-red: #990000;
    --text-light: #ffffff;
  }
  * { margin: 0; padding: 0; box-sizing: border-box; }
  html, body { width: 1200px; height: 1200px; overflow: hidden; }
  body {
    background: var(--canvas);
    font-family: "Montserrat", sans-serif;
    position: relative;
  }
  .card {
    position: absolute;
    left: 200px;
    width: 800px;
    height: 457px;
    border-radius: 24px;
    overflow: hidden;
  }
  .card--front { top: 87px; background: var(--ink); }
  .card--back { top: 656px; background: var(--brand-red); color: var(--text-light); }

  .front-shape { position: absolute; inset: 0; }

  .owner-name {
    position: absolute;
    left: 45px; top: 145px;
    font-family: "Michroma", sans-serif;
    font-weight: 400;
    font-size: 21px;
    letter-spacing: 0.3px;
    color: var(--brand-red);
    white-space: nowrap;
  }
  .contact-list {
    position: absolute;
    left: 45px; top: 204px;
    list-style: none;
    color: var(--text-light);
    font-size: 18px;
    font-weight: 500;
    line-height: 22.5px;
  }
  .contact-list li { display: flex; align-items: center; gap: 10px; white-space: nowrap; }
  .contact-list li.gap-after { margin-bottom: 14px; }
  .contact-list svg { width: 16px; height: 16px; flex: none; fill: var(--brand-red); }

  .brand {
    position: absolute;
    text-align: center;
    font-family: "Montserrat", sans-serif;
    font-weight: 500;
    white-space: nowrap;
  }
  .brand-mark {
    display: block;
    margin: 0 auto;
    border-radius: 50%;
  }
  .brand-name { display: block; font-size: 33px; letter-spacing: 2px; line-height: 1.1; }
  .brand-sub { display: block; font-size: 18px; letter-spacing: 14px; margin-right: -14px; line-height: 1.2; }

  .brand--front { left: 426px; width: 300px; top: 148px; color: var(--ink); }
  .brand--front .brand-mark { width: 96px; height: 96px; border: 9px solid var(--brand-red); margin-bottom: 12px; }
  .brand--front .brand-sub { color: var(--brand-red); }

  .brand--back { left: 225px; width: 350px; top: 118px; color: var(--text-light); }
  .brand--back .brand-mark { width: 112px; height: 112px; border: 10px solid var(--text-light); margin-bottom: 14px; }
  .brand--back .brand-name { font-size: 38px; letter-spacing: 2px; }
  .brand--back .brand-sub { font-size: 20px; letter-spacing: 17px; margin-right: -17px; }

  .services {
    position: absolute;
    left: 0; right: 0; top: 339px;
    text-align: center;
  }
  .services-title { font-weight: 700; font-size: 18px; letter-spacing: 0.3px; margin-bottom: 8px; }
  .services-list { font-size: 18px; font-weight: 400; line-height: 24px; }
  .dot { display: inline-block; width: 7px; height: 7px; border-radius: 50%; background: var(--text-light); margin: 0 8px 2px; vertical-align: middle; }
</style>
</head>
<body>

<section class="card card--front" aria-label="Business card front">
  <svg class="front-shape" viewBox="0 0 800 457" aria-hidden="true">
    <circle cx="571" cy="228" r="236" fill="var(--brand-red)"/>
    <circle cx="571" cy="228" r="231" fill="var(--paper)"/>
    <rect x="571" y="0" width="229" height="457" fill="var(--paper)"/>
  </svg>

  <h1 class="owner-name">MARK DUNROW</h1>
  <ul class="contact-list">
    <li class="gap-after">
      <svg viewBox="0 0 16 16"><path d="M8 1a5 5 0 0 0-5 5c0 3.6 5 9 5 9s5-5.4 5-9a5 5 0 0 0-5-5zm0 7a2 2 0 1 1 0-4 2 2 0 0 1 0 4z"/></svg>
      Kelmore Bay, Sk
    </li>
    <li>
      <svg viewBox="0 0 16 16"><path d="M3.6 1.5l2.3 2.6-1.3 1.8c.9 2 2.5 3.6 4.5 4.5l1.8-1.3 2.6 2.3-1.3 2.1C7 13.3 2.7 9 2 3z"/></svg>
      (403)271-6094
    </li>
    <li>
      <svg viewBox="0 0 16 16"><path d="M2 4h12v1L8 9 2 5zm0 2.5l6 4 6-4V12H2z"/></svg>
      info@shinefoxautocare.com
    </li>
    <li>
      <svg viewBox="0 0 16 16"><circle cx="8" cy="8" r="6.5"/></svg>
      www.shinefoxautocare.com
    </li>
  </ul>

  <div class="brand brand--front">
    <span class="brand-mark" aria-hidden="true"></span>
    <span class="brand-name">SHINE FOX</span>
    <span class="brand-sub">AUTO CARE</span>
  </div>
</section>

<section class="card card--back" aria-label="Business card back">
  <div class="brand brand--back">
    <span class="brand-mark" aria-hidden="true"></span>
    <span class="brand-name">SHINE FOX</span>
    <span class="brand-sub">AUTO CARE</span>
  </div>
  <div class="services">
    <p class="services-title">COMPLETE INTERIOR &amp; EXTERIOR DETAIL</p>
    <p class="services-list">Paint correction &amp; Protection<span class="dot"></span>Ceramic coating<br>Trim restore<span class="dot"></span>Auto carpet &amp; Seat cleaning</p>
  </div>
</section>

</body>
</html>
```